Copper Lantern

Need a business card for our restaurant. Restaurant and Bar in the mountains of North Idaho. Rustic looking card

rustic design, wood and metal looking, primarily neutral colors

• Name, address, phone number, website, email address

```html
<!DOCTYPE html>
<html lang="en">
<head>
<meta charset="utf-8">
<title>Copper Lantern – Business Card</title>
<link href="https://fonts.googleapis.com/css2?family=Montserrat:wght@400;700&display=swap" rel="stylesheet">
<style>
  :root {
    --stage: #1e1c1a;
    --wood-dark: #221b16;
    --wood-mid: #33291f;
    --wood-light: #45382b;
    --grain-dark: rgba(0,0,0,0.28);
    --grain-light: rgba(255,235,210,0.05);
    --metal-light: #c9c6c0;
    --metal-mid: #8e8a83;
    --metal-dark: #4e4b47;
    --ink: #f2ede6;
    --ink-soft: #cfc7bc;
    --mark-faint: rgba(201,198,192,0.22);
  }
  * { margin: 0; padding: 0; box-sizing: border-box; }
  html, body { width: 1200px; height: 875px; overflow: hidden; }
  body {
    background: var(--stage);
    font-family: "Montserrat", sans-serif;
    position: relative;
  }

  .card {
    position: absolute;
    width: 560px;
    height: 320px;
    border-radius: 18px;
    overflow: hidden;
    box-shadow: 0 20px 40px rgba(0,0,0,0.55);
    background:
      repeating-linear-gradient(91deg, var(--grain-light) 0 2px, transparent 2px 9px),
      repeating-linear-gradient(89deg, var(--grain-dark) 0 1px, transparent 1px 17px),
      repeating-linear-gradient(90.5deg, rgba(0,0,0,0.18) 0 3px, transparent 3px 41px),
      linear-gradient(180deg, var(--wood-light) 0%, var(--wood-mid) 45%, var(--wood-dark) 100%);
  }
  .card-front { left: 60px; top: 90px; }
  .card-back  { left: 580px; top: 465px; }

  .metal-rim {
    position: absolute;
    inset: 10px;
    border-radius: 11px;
    border: 3px solid var(--metal-mid);
    box-shadow:
      inset 0 0 0 1px var(--metal-dark),
      0 0 0 1px rgba(0,0,0,0.5),
      inset 0 1px 0 1px rgba(255,255,255,0.15);
    pointer-events: none;
  }

  .pattern-area {
    position: absolute;
    left: 24px; top: 24px; right: 24px; bottom: 24px;
    border-radius: 6px;
    background:
      repeating-linear-gradient(0deg, rgba(255,255,255,0.05) 0 1px, transparent 1px 3px),
      linear-gradient(115deg, var(--metal-light) 0%, var(--metal-mid) 25%, var(--metal-dark) 55%, rgba(40,34,28,0.4) 100%);
    opacity: 0.45;
  }
  .front-mark {
    position: absolute;
    right: 150px;
    top: 142px;
    font-weight: 700;
    font-size: 15px;
    color: var(--ink);
    letter-spacing: 0.5px;
  }

  .brand {
    position: absolute;
    left: 34px;
    top: 40px;
    display: flex;
    align-items: center;
    gap: 10px;
  }
  .brand-dot {
    width: 14px; height: 14px; border-radius: 50%;
    background: var(--metal-light);
  }
  .brand-name {
    font-weight: 700;
    font-size: 17px;
    color: var(--ink);
  }
  .brand-tag {
    position: absolute;
    left: 58px; top: 66px;
    font-size: 9px;
    letter-spacing: 2px;
    color: var(--ink-soft);
  }
  .metal-bar {
    position: absolute;
    left: 34px; top: 90px;
    width: 210px; height: 4px;
    border-radius: 2px;
    background: linear-gradient(90deg, var(--metal-dark), var(--metal-light) 50%, var(--metal-dark));
  }

  .person { position: absolute; left: 34px; top: 118px; color: var(--ink); }
  .person-name { font-weight: 700; font-size: 22px; }
  .person-role { font-size: 12px; color: var(--ink-soft); margin-top: 2px; }
  .address { font-size: 12px; color: var(--ink-soft); margin-top: 10px; line-height: 1.35; }
  .contacts { list-style: none; margin-top: 10px; font-size: 12px; color: var(--ink-soft); }
  .contacts li { display: flex; align-items: center; gap: 8px; line-height: 1.6; }
  .contacts svg { width: 11px; height: 11px; fill: var(--metal-light); }

  .back-mark {
    position: absolute;
    right: 40px;
    top: 120px;
    font-weight: 700;
    font-size: 40px;
    color: var(--mark-faint);
    text-align: right;
    line-height: 1.05;
  }
</style>
</head>
<body>

  <section class="card card-front">
    <div class="pattern-area" role="img" aria-label="Repeating brushed-metal pattern of the restaurant emblem"></div>
    <div class="metal-rim"></div>
    <div class="front-mark">Copper Lantern</div>
  </section>

  <section class="card card-back">
    <div class="metal-rim"></div>
    <div class="brand">
      <span class="brand-dot"></span>
      <span class="brand-name">Copper Lantern</span>
    </div>
    <div class="brand-tag">RESTAURANT AND BAR</div>
    <div class="metal-bar"></div>

    <div class="person">
      <div class="person-name">Mara Holloway</div>
      <div class="person-role">Managing Director</div>
      <div class="address">48 Ridge Road,<br>Pine Hollow, ID</div>
      <ul class="contacts">
        <li><svg viewBox="0 0 12 12"><path d="M2 1h3l1 3-1.5 1a7 7 0 0 0 2.5 2.5L8 6l3 1v3a1 1 0 0 1-1 1A9 9 0 0 1 1 2a1 1 0 0 1 1-1z"/></svg>(208) 555 0147</li>
        <li><svg viewBox="0 0 12 12"><path d="M1 3h10v7H1z"/><path d="M1 3l5 4 5-4" fill="none" stroke="#33291f" stroke-width="1"/></svg>hello@copperlantern.com</li>
        <li><svg viewBox="0 0 12 12"><circle cx="6" cy="6" r="5"/></svg>www.copperlantern.com</li>
      </ul>
    </div>

    <div class="back-mark">Copper<br>Lantern</div>
  </section>

</body>
</html>
```